Website Design for Wheels for Servicemen.org - Donated Cars to Disabled Vets

Need a Wordpress website. The coding now, esp. the CDONT coding is not supported by many hosting sites. Looking for a landing page to generate leads.

Logo Text

look at current one for ideas

Coding

Coded - Design and coding required

Number of Pages Required

1 page

Requirements
Must have
• look at current website at www.wheelsforservicemen.org
Nice to have
• look at this site: http://givevehicletoservicemen.org

```html
<!DOCTYPE html>
<html lang="en">
<head>
<meta charset="utf-8">
<title>Wheels for Servicemen.org – Donate Your Car to Veterans</title>
<link rel="stylesheet" href="https://fonts.googleapis.com/css2?family=Lato:wght@300;400;700;900&display=swap">
<style>
:root{
  --red:#c8161d;
  --red-dark:#8e0b10;
  --red-bright:#e5202a;
  --blue:#1565c0;
  --blue-dark:#0d47a1;
  --text:#444;
  --muted:#8a8a8a;
  --light:#f2f2f2;
  --white:#fff;
}
*{box-sizing:border-box;margin:0;padding:0}
html,body{width:686px;height:1200px;overflow:hidden;background:var(--white);font-family:"Lato",sans-serif;color:var(--text)}
.page{position:relative;width:686px;height:1200px}
.abs{position:absolute}

/* header */
.brand{left:86px;top:22px;display:flex;align-items:center;gap:6px}
.brand-mark{width:14px;height:14px;border-radius:50%;background:var(--red)}
.brand-name{font-size:15px;font-weight:700;color:var(--blue)}
.call{right:86px;top:25px;text-align:right}
.call-label{font-size:10px;color:var(--red)}
.call-number{display:flex;align-items:center;gap:4px;font-size:15px;color:var(--blue)}

/* nav */
.nav{left:0;top:67px;width:686px;height:31px;background:var(--red)}
.nav ul{position:absolute;left:85px;top:0;display:flex;list-style:none;height:31px}
.nav li{height:31px;line-height:31px;font-size:9px;font-weight:700;color:var(--white);text-align:center;border-right:1px solid rgba(0,0,0,.15)}
.nav li.active{background:var(--red-dark)}

/* hero */
.hero{left:0;top:98px;width:686px;height:259px;background:linear-gradient(100deg,#bcd0e0 0%,#d9cfcf 35%,#b89c86 55%,#9fb1c5 100%)}
.hero-title{left:87px;top:207px;font-weight:900}
.hero-title .l1{display:block;font-size:19px;line-height:22px;color:var(--blue)}
.hero-title .l2{display:block;font-size:23px;line-height:26px;color:var(--red)}
.dots{left:90px;top:266px;display:flex;gap:5px}
.dots span{width:7px;height:7px;border-radius:50%;background:#111}
.dots span:first-child{background:var(--white);border:1.5px solid #111}

.donate{left:418px;top:123px;width:183px;height:205px;background:var(--blue)}
.donate-head{height:36px;background:var(--blue-dark);color:var(--white);font-size:12.5px;text-align:center;line-height:30px;clip-path:polygon(0 0,100% 0,100% 80%,50% 100%,0 80%)}
.field{position:absolute;height:18px;background:var(--white);font-size:6.5px;color:#999;padding-left:7px;line-height:18px}
.donate-btn{position:absolute;left:12px;top:168px;width:163px;height:22px;background:var(--red-bright);color:var(--white);font-size:9px;font-weight:700;text-align:center;line-height:22px}

/* steps */
.step{width:180px;text-align:center}
.step-ring{width:92px;height:92px;margin:0 auto;border-radius:50%;background:var(--white);border:1px solid #ddd;display:flex;align-items:center;justify-content:center}
.step-ring div{width:76px;height:76px;border-radius:50%;border:2px solid var(--blue);display:flex;align-items:center;justify-content:center}
.step h3{margin-top:12px;font-size:13px;font-weight:400;color:var(--blue)}
.step h3 b{color:var(--red);font-weight:400}
.step p{width:142px;margin:6px auto 0;font-size:7px;line-height:1.6;color:var(--muted)}

/* why section */
.why{left:0;top:552px;width:686px;height:243px;background:linear-gradient(120deg,#a8131a 0%,#b8171e 50%,#a01218 100%)}
.why-notch{left:328px;top:552px;width:30px;height:17px;background:var(--white);clip-path:polygon(0 0,100% 0,50% 100%)}
.why-title{left:0;width:686px;top:584px;text-align:center;color:var(--white);font-size:15px;font-weight:700}
.feature{color:var(--white);display:flex;gap:8px}
.feature h4{font-size:11px;font-weight:700}
.feature p{font-size:8px;line-height:1.4;margin-top:4px;color:#f3dede}
.btn-outline{left:307px;top:755px;width:87px;height:21px;border:1.5px solid var(--white);color:var(--white);font-size:8px;font-weight:700;text-align:center;line-height:18px}

/* program */
.program{left:0;top:795px;width:686px;height:220px;background:var(--light)}
.program-title{left:0;width:686px;top:815px;text-align:center;font-size:16px;font-weight:400;color:#444}
.card{top:850px;width:122px;height:130px;background:var(--white);border:1px solid #e2e2e2}
.card-img{height:68px}
.card h5{padding:8px 10px 0;font-size:8px;font-weight:400;color:var(--blue);line-height:1.3}
.card p{padding:3px 10px 0;font-size:6px;color:#999;line-height:1.4}

/* footer */
.fcol h6{font-size:12px;font-weight:400;color:var(--blue);margin-bottom:9px}
.fcol li{list-style:none;font-size:8px;color:#666;margin-bottom:6px}
.fcol p{font-size:8px;color:#666}
.socials{display:flex;gap:5px;margin-top:8px}
.socials span{width:17px;height:17px;border-radius:50%}
.rule{left:86px;top:1162px;width:514px;height:1px;background:#ddd}
.copy{left:0;width:686px;top:1175px;text-align:center;font-size:7.5px;color:#999}
</style>
</head>
<body>
<div class="page">

  <header>
    <div class="abs brand"><span class="brand-mark"></span><span class="brand-name">Wheels for Servicemen</span></div>
    <div class="abs call">
      <div class="call-label">Call Us Today</div>
      <div class="call-number">
        <svg width="11" height="11" viewBox="0 0 24 24"><path fill="#c8161d" d="M6.6 10.8a15 15 0 0 0 6.6 6.6l2.2-2.2c.3-.3.7-.4 1-.2 1.1.4 2.3.6 3.6.6.6 0 1 .4 1 1V20c0 .6-.4 1-1 1C10.6 21 3 13.4 3 4c0-.6.4-1 1-1h3.5c.6 0 1 .4 1 1 0 1.3.2 2.5.6 3.6.1.3 0 .7-.2 1z"/></svg>
        1800-555-0142
      </div>
    </div>
  </header>

  <nav class="abs nav">
    <ul>
      <li class="active" style="width:83px">HOME</li>
      <li style="width:80px">ABOUT US</li>
      <li style="width:80px">SERVICES</li>
      <li style="width:97px">DONATE CAR</li>
      <li style="width:67px">WHY US</li>
      <li style="width:83px">CONTACT US</li>
    </ul>
  </nav>

  <section class="abs hero" role="img" aria-label="Smiling couple, a soldier in camouflage and a woman holding car keys, in front of rows of American flags"></section>
  <h1 class="abs hero-title"><span class="l1">DONATE YOUR CAR</span><span class="l2">TO VETERANS</span></h1>
  <div class="abs dots"><span></span><span></span><span></span><span></span></div>

  <form class="abs donate">
    <div class="donate-head">Want to Donate Now</div>
    <div class="field" style="left:12px;top:49px;width:163px">Name</div>
    <div class="field" style="left:12px;top:72px;width:163px">Email</div>
    <div class="field" style="left:12px;top:96px;width:80px">Phone</div>
    <div class="field" style="left:95px;top:96px;width:80px">Cell phone</div>
    <div class="field" style="left:12px;top:119px;width:80px">City</div>
    <div class="field" style="left:95px;top:119px;width:80px">Address</div>
    <div class="field" style="left:12px;top:142px;width:80px">State</div>
    <div class="field" style="left:95px;top:142px;width:80px">Zip Code</div>
    <div class="donate-btn">DONATE NOW</div>
  </form>

  <section>
    <div class="abs step" style="left:72px;top:337px">
      <div class="step-ring"><div>
        <svg width="34" height="34" viewBox="0 0 24 24"><path fill="none" stroke="#c8161d" stroke-width="1.5" d="M4 3h16v13h-9l-4 4v-4H4z"/><path fill="#c8161d" d="M9 7c.5 2 1.8 3.4 3.8 4l.9-.9c.2-.2.4-.2.6-.1l1.4.5v1.6c0 .3-.2.5-.5.5C11.4 12.6 8.4 9.6 8.4 5.8c0-.3.2-.5.5-.5h1.6l.5 1.4-.9.9z"/></svg>
      </div></div>
      <h3><b>1.</b> Call Us Now</h3>
      <p>Anterdum vel blandit sed nulla In ullamcorper est eget tempor cursus neque mi consectetuer mi a ultricie</p>
    </div>
    <div class="abs step" style="left:249px;top:337px">
      <div class="step-ring"><div>
        <svg width="40" height="30" viewBox="0 0 40 30"><path fill="#c8161d" d="M18 8l16 4-3 14H18l-4-6z"/><circle cx="21" cy="21" r="4" fill="#fff" stroke="#c8161d" stroke-width="2"/><path stroke="#c8161d" stroke-width="2" d="M3 3l12 14"/><circle cx="3" cy="3" r="2" fill="#c8161d"/></svg>
      </div></div>
      <h3><b>2.</b> We Tow it</h3>
      <p>Anterdum vel blandit sed nulla In ullamcorper est eget tempor cursus neque mi consectetuer mi a ultricie</p>
    </div>
    <div class="abs step" style="left:433px;top:337px">
      <div class="step-ring"><div>
        <svg width="30" height="34" viewBox="0 0 24 28"><path fill="none" stroke="#c8161d" stroke-width="1.5" d="M5 2h12l4 4v16H5z"/><text x="9" y="14" font-size="9" fill="#c8161d" font-family="Lato,sans-serif" font-weight="700">%</text><path fill="none" stroke="#c8161d" stroke-width="2" d="M2 20l3 4 6-7"/></svg>
      </div></div>
      <h3><b>3.</b> Tax Write Off</h3>
      <p>Anterdum vel blandit sed nulla In ullamcorper est eget tempor cursus neque mi consectetuer mi a ultricie</p>
    </div>
  </section>

  <section class="abs why" role="img" aria-label="Red-tinted photo of a soldier hugging a smiling child"></section>
  <div class="abs why-notch"></div>
  <h2 class="abs why-title">Why Donate Your Car to Us?</h2>

  <div class="abs feature" style="left:106px;top:625px;width:210px">
    <svg width="22" height="22" viewBox="0 0 22 22"><rect x="1" y="3" width="18" height="18" fill="none" stroke="#fff" stroke-width="1.6"/><path d="M5 11l4 4 11-13" fill="none" stroke="#fff" stroke-width="2.2"/></svg>
    <div><h4>IRS 501(c)3 Approved:</h4><p>Free 24/7 Pickup with No DMV Hassles.</p></div>
  </div>
  <div class="abs feature" style="left:350px;top:630px;width:250px">
    <svg width="22" height="36" viewBox="0 0 22 36"><path d="M4 2h14M6 6h10M11 6v12" stroke="#fff" stroke-width="2.2" fill="none"/><path d="M11 18c-4 0-6 3-6 6s2 7 6 7 6-3 6-6" stroke="#fff" stroke-width="2.4" fill="none"/></svg>
    <div><h4>Free Local Towing to You</h4><p>We will pick up your car donation, running or not, when it's most convenient, at home or work</p></div>
  </div>
  <div class="abs feature" style="left:98px;top:690px;width:230px">
    <svg width="30" height="24" viewBox="0 0 30 24"><path fill="#fff" d="M4 10l4-7h14l4 7h2v8h-3v4h-4v-4H9v4H5v-4H2v-8z"/><path fill="#b8171e" d="M9 5h12l3 5H6z"/><circle cx="7" cy="14" r="1.8" fill="#b8171e"/><circle cx="23" cy="14" r="1.8" fill="#b8171e"/></svg>
    <div><h4>All Cars Accepted</h4><p>We take your car regardless of its condition or registration status.</p></div>
  </div>
  <div class="abs feature" style="left:348px;top:690px;width:270px">
    <svg width="30" height="30" viewBox="0 0 30 30"><path d="M12 1v10M8 7l4 4 4-4" stroke="#fff" stroke-width="2" fill="none"/><ellipse cx="7" cy="23" rx="5" ry="2" fill="#fff"/><ellipse cx="7" cy="27" rx="5" ry="2" fill="#fff"/><ellipse cx="17" cy="17" rx="5" ry="2" fill="#fff"/><ellipse cx="17" cy="21" rx="5" ry="2" fill="#fff"/><ellipse cx="17" cy="25" rx="5" ry="2" fill="#fff"/><ellipse cx="26" cy="23" rx="4" ry="2" fill="#fff"/><ellipse cx="26" cy="27" rx="4" ry="2" fill="#fff"/></svg>
    <div><h4>Income Tax Deduction</h4><p>We issue you an IRS tax receipt &amp; offer the largest resale network to get you the highest tax write-off possible.</p></div>
  </div>
  <div class="abs btn-outline">VIEW MORE</div>

  <section class="abs program"></section>
  <h2 class="abs program-title">Car Donation Program</h2>
  <article class="abs card" style="left:86px">
    <div class="card-img" role="img" aria-label="Dark blue globe map with network lines" style="background:linear-gradient(135deg,#0b2030,#1d4a5a)"></div>
    <h5>Donation Accepted Nationalwide</h5>
    <p>Curabitur iaculis tempus eros Cura bitur vel mi sit amet magna</p>
  </article>
  <article class="abs card" style="left:216px">
    <div class="card-img" role="img" aria-label="Black SUV on an autumn road" style="background:linear-gradient(135deg,#c9952e,#3a3a3a 60%,#8a7040)"></div>
    <h5>All Vehicles Type Welcome</h5>
    <p>Curabitur iaculis tempus eros Cura bitur vel mi sit amet magna</p>
  </article>
  <article class="abs card" style="left:346px">
    <div class="card-img" role="img" aria-label="Calculator and pen on paperwork" style="background:linear-gradient(135deg,#8a8a8a,#d8d8d8 60%,#b9a58e)"></div>
    <h5>We take care of all Paperwork.</h5>
    <p>Curabitur iaculis tempus eros Cura bitur vel mi sit amet magna</p>
  </article>
  <article class="abs card" style="left:476px">
    <div class="card-img" role="img" aria-label="Soldier holding a child with a small flag outdoors" style="background:linear-gradient(135deg,#4f7a3a,#9a8a70 60%,#5c8a46)"></div>
    <h5>And we take care of DMV &amp; Smog issues.</h5>
    <p>Curabitur iaculis tempus eros Cura bitur vel mi sit amet magna</p>
  </article>

  <footer>
    <div class="abs fcol" style="left:92px;top:1042px">
      <h6>Quick Links</h6>
      <ul><li>About Us</li><li>What We Do</li><li>How it works</li><li>Members</li></ul>
    </div>
    <div class="abs fcol" style="left:214px;top:1042px">
      <h6>Resources</h6>
      <ul><li>Support</li><li>FAQ</li><li>Term of Use</li><li>Contact Us</li></ul>
    </div>
    <div class="abs fcol" style="left:330px;top:1042px">
      <h6>Connect With Us</h6>
      <p>Please connect with us on these</p>
      <div class="socials">
        <span style="background:#55acee"></span><span style="background:#2b4b8f"></span><span style="background:#1f6f8b"></span><span style="background:#d64a34"></span>
      </div>
    </div>
    <div class="abs" style="left:485px;top:1042px;width:26px;height:26px;border-radius:4px;background:#c8161d"></div>
    <div class="abs" style="left:503px;top:1087px;width:32px;height:32px;border-radius:50%;background:#5a9bd5"></div>
    <div class="abs rule"></div>
    <div class="abs copy">© 2016 Company Name  All right reserved</div>
  </footer>

</div>
</body>
</html>
```